UK Online Auction Site needs a clever design

We need a contemporary landing page and registration page design for a UK auction website, that look equally at home on PC's and tablets . The design should be fresh, bright, clean, professional, robust, and familiar. We would like to see something clever but functional.

Online

```html
<!DOCTYPE html>
<html lang="en"><head><meta charset="utf-8"><title>Bidwell – UK Online Auctions</title>
<link href="https://fonts.googleapis.com/css2?family=Open+Sans:wght@400;600;700&display=swap" rel="stylesheet">
<style>
:root{--blue:#1a82d0;--blue-dk:#0f6fb8;--dark:#222;--foot:#3a3a3a;--foot-dk:#2b2b2b;--line:#d6d6d6;--text:#333;--muted:#777;--star:#f7941d;--header:#f2f2f2}
*{box-sizing:border-box;margin:0;padding:0}
html,body{width:798px;height:1200px;overflow:hidden}
body{font-family:'Open Sans',sans-serif;color:var(--text);background:#fff;position:relative;font-size:8px}
.abs{position:absolute}
.topbar{left:0;top:0;width:798px;height:26px;background:var(--dark);color:#fff;font-size:7px}
.topbar a{color:#fff;text-decoration:none;position:absolute;top:9px}
.topbar .pill{position:absolute;top:6px;height:14px;padding:0 6px;background:#333;border-radius:2px;line-height:14px}
.header{left:0;top:26px;width:798px;height:113px;background:var(--header)}
.brand{left:130px;top:50px;height:36px;display:flex;align-items:center;gap:6px;font-size:26px;font-weight:700;color:var(--blue)}
.brand i{width:14px;height:14px;border-radius:50%;background:var(--blue);display:block}
.search{left:364px;top:57px;width:315px;height:29px;border:1px solid #d0d0d0;border-radius:15px;background:#fff;overflow:hidden;display:flex}
.search .cat{width:93px;background:#ececec;border-right:1px solid #d0d0d0;font-size:7px;line-height:27px;padding-left:22px}
.search .cat:after{content:"";display:inline-block;margin-left:8px;border:3px solid transparent;border-top:4px solid var(--blue);vertical-align:-1px}
.search .field{flex:1;color:#bbb;font-size:7px;line-height:27px;padding-left:10px}
.sidebar{left:115px;top:110px;width:184px;height:261px;border:2px solid var(--blue);border-radius:3px;background:#fff}
.sidebar h3{height:28px;background:#f3f3f3;border-bottom:1px solid var(--line);font-size:8px;font-weight:600;line-height:27px;padding-left:13px;position:relative}
.sidebar h3:after{content:"";position:absolute;right:13px;top:12px;border:3px solid transparent;border-top:4px solid #333}
.sidebar li{list-style:none;height:25.2px;line-height:25px;padding-left:21px;margin:0 2px;border-bottom:1px solid #e4e4e4;font-size:7.5px;position:relative}
.sidebar li:last-child{border-bottom:0}
.sidebar li:after{content:"";position:absolute;right:12px;top:11px;border:3px solid transparent;border-left:4px solid var(--blue)}
.sidebar li.first{font-weight:600}
.nav{left:304px;top:111px;width:381px;height:28px;background:var(--blue);border-radius:2px;display:flex;align-items:center;color:#fff;font-size:8px;padding-left:8px}
.nav span{padding:0 14px;border-right:1px solid rgba(255,255,255,.3);line-height:14px}
.nav span:nth-child(6){border:0}
.nav .cart{margin-left:auto;border:0;padding-right:10px}
.slider{left:304px;top:156px;width:375px;height:205px;background:linear-gradient(100deg,#e0151b 0 30%,#f4f4f4 30% 100%);box-shadow:0 3px 4px rgba(0,0,0,.2)}
.arrow{top:225px;width:48px;height:48px;border-radius:50%;background:#111}
.dots{top:346px;left:626px;display:flex;gap:8px}
.dots b{width:6px;height:6px;border-radius:50%;background:#fff;display:block}
.dots b.on{box-shadow:0 0 0 2px #333 inset,0 0 0 1px #fff}
.box{top:402px;width:155px;height:123px;border:1px solid var(--line);background:#fff}
.box h4{height:29px;border-bottom:1px solid var(--line);font-size:9px;font-weight:600;line-height:28px;padding-left:11px}
.box p{font-size:7px;line-height:13.6px;padding:8px 11px 0;color:#333}
.box .btn{position:absolute;right:-1px;bottom:-1px;height:25px;padding:0 9px;border:1px solid var(--line);background:#fafafa;font-size:8px;line-height:24px}
.box .btn:after{content:"";display:inline-block;margin-left:5px;border:3px solid transparent;border-left:4px solid var(--blue)}
.box ul li{list-style:none;font-size:7.5px;height:29px;line-height:29px;padding-left:38px;position:relative}
.box ul svg{position:absolute;left:17px;top:6px}
.promo{left:115px;top:540px;width:568px;height:48px;background:linear-gradient(90deg,#6b3a22,#c98a55 30%,#8a6247 55%,#5d4332 75%,#c8805a)}
.promo .tag{position:absolute;right:6px;top:4px;width:126px;height:40px;background:rgba(200,60,140,.85);color:#fff;padding:4px 9px}
.promo .tag b{font-size:11px;display:block;line-height:13px}
.promo .tag span{font-size:7px}
.sect{left:120px;font-size:10px;color:#333}
.card{width:118px;height:160px;border:1px solid var(--line);background:#fafafa;overflow:hidden}
.card .img{position:absolute;left:4px;top:4px;width:108px;height:100px}
.card .stars{position:absolute;left:6px;top:99px;font-size:11px;color:var(--star);letter-spacing:-1px}
.card .stars i{color:#888;font-style:normal}
.card .name{position:absolute;left:9px;top:122px;font-size:7.5px}
.card .price{position:absolute;left:9px;top:142px;font-size:8px}
.card .price s{color:#999;margin-right:2px}
.card .corner{position:absolute;right:-1px;bottom:-1px;width:34px;height:34px;background:#d6d6d6;border-top-left-radius:34px}
.card .corner svg{position:absolute;right:6px;bottom:6px}
.card.active .corner{background:var(--blue)}
.card.active .name{color:var(--blue)}
.sl{width:12px;height:12px;background:#e2e2e2;border:1px solid #ccc}
.sl:after{content:"";position:absolute;top:3px;left:3px;border:3px solid transparent}
.sl.l:after{border-right:3px solid #888;left:1px}
.sl.r:after{border-left:3px solid #555;left:4px}
.footer{left:0;top:1039px;width:798px;height:120px;background:var(--foot);color:#ddd}
.footer h5{font-size:9.5px;font-weight:400;color:#fff;margin-bottom:4px}
.footer .col{position:absolute;top:20px}
.footer .col div{font-size:7.5px;line-height:14.6px;padding-left:14px}
.bottom{left:0;top:1159px;width:798px;height:41px;background:var(--foot-dk);color:#ccc;font-size:6.5px}
.soc{top:7px;width:27px;height:27px;border-radius:3px}
</style></head><body>
<div class="abs topbar"><a style="left:120px">About Us</a><a style="left:160px">Contact Us</a>
<svg class="abs" style="left:534px;top:10px" width="7" height="7" viewBox="0 0 10 10"><path d="M2 0l2 3-1 1c1 2 2 3 3 3l1-1 3 2-1 2C4 10 0 6 0 1z" fill="#fff"/></svg>
<a style="left:545px">020 555 0147</a><span class="pill" style="left:596px">English ⌄</span><span class="pill" style="left:650px">USD ⌄</span></div>
<div class="abs header"></div>
<div class="abs brand"><i></i>Bidwell</div>
<div class="abs search"><div class="cat">All Categories</div><div class="field">Search.....</div>
<svg style="margin:10px 12px 0 0" width="8" height="8" viewBox="0 0 10 10"><circle cx="4" cy="4" r="3" fill="none" stroke="#1a82d0" stroke-width="1.6"/><path d="M6 6l3 3" stroke="#1a82d0" stroke-width="1.6"/></svg></div>
<div class="abs sidebar"><h3>Shop By Category</h3><ul>
<li class="first">All Categories</li><li>Fashion</li><li>Home &amp; Garden</li><li>Electricals @ Technology</li><li>Collectables &amp; Antiques</li><li>Jewellery @ Beauty</li><li>Toys</li><li>Sport &amp; Leisure</li><li>Motors</li></ul></div>
<div class="abs nav"><span>Home</span><span>Sell</span><span>Sign In</span><span>Login</span><span>Favourite</span><span>Help</span><span class="cart">🛒︎ (0) ▾</span></div>
<div class="abs slider" role="img" aria-label="Sale banner: up to 60% off footwear, shoes and a shopping couple"></div>
<div class="abs arrow" style="left:280px"><svg class="abs" style="left:28px;top:19px" width="8" height="10"><path d="M6 1L2 5l4 4" stroke="#fff" fill="none" stroke-width="1.4"/></svg></div>
<div class="abs arrow" style="left:653px"><svg class="abs" style="left:13px;top:19px" width="8" height="10"><path d="M2 1l4 4-4 4" stroke="#fff" fill="none" stroke-width="1.4"/></svg></div>
<div class="abs dots"><b></b><b class="on"></b><b></b></div>
<div class="abs box" style="left:119px"><h4>Welcome</h4><p>Even if you're new or already experi-enced, we have everything you need to enjoy shopping on bidwell.co.uk.</p><div class="btn">More</div></div>
<div class="abs box" style="left:325px"><h4>Sign In</h4><p>Sign-in to your account in order to buy, sell or manage your preferences.</p><p style="font-size:6.5px;padding-top:5px">Don't have an account? <b style="color:var(--blue);font-weight:600">Register ›</b></p><div class="btn">Sign In</div></div>
<div class="abs box" style="left:524px"><h4>Shop with confidence</h4><ul>
<li><svg width="14" height="17" viewBox="0 0 14 17"><path d="M7 0l7 3v6c0 4-3 7-7 8-4-1-7-4-7-8V3z" fill="#222"/><rect x="6" y="5" width="2" height="6" fill="#fff"/></svg>Completely safe</li>
<li><svg width="14" height="18" viewBox="0 0 14 18"><circle cx="7" cy="6" r="6" fill="#222"/><path d="M3 10l-2 8 4-2 2 2 2-2 4 2-2-8z" fill="#222"/><circle cx="7" cy="6" r="3" fill="#fff"/></svg>Premium sellers</li>
<li><svg width="16" height="17" viewBox="0 0 16 17"><path d="M7 1l2 4 4 .5-3 3 1 4-4-2-4 2 1-4-3-3 4-.5z" fill="none" stroke="#222"/><circle cx="12" cy="13" r="3.5" fill="#fff" stroke="#222"/></svg>Feedback rating system</li></ul></div>
<div class="abs promo" role="img" aria-label="Camera promotion photo with hair and lens"><div class="tag"><b>LUMORA CAMERA</b><span>Shop all cameras &amp; camcorders</span></div></div>
<div class="abs sect" style="top:608px">FEATURED PRODUCTS</div>
<div class="abs sl l" style="left:114px;top:721px"></div><div class="abs sl r" style="left:672px;top:721px"></div>
<div class="abs card active" style="left:137px;top:638px"><div class="img" role="img" aria-label="Navy sports bag" style="background:radial-gradient(#2a4a7a 35%,#f5f5f5 60%)"></div><div class="name">BAG</div><div class="price"><s>$22</s>$19</div><div class="corner"><svg width="16" height="13" viewBox="0 0 16 13"><path d="M0 1h3l2 7h8l2-5H5" fill="none" stroke="#fff" stroke-width="1.5"/><circle cx="6" cy="11" r="1.3" fill="#fff"/><circle cx="12" cy="11" r="1.3" fill="#fff"/></svg></div></div>
<div class="abs card" style="left:269px;top:638px"><div class="img" role="img" aria-label="Dark aviator sunglasses" style="background:radial-gradient(ellipse 60% 25%,#1f2a2a 60%,#f6f6f6 75%)"></div><div class="stars">★★★★<i>★</i></div><div class="name">WOMAN GLASSES</div><div class="price">$39</div><div class="corner"><svg width="16" height="13" viewBox="0 0 16 13"><path d="M0 1h3l2 7h8l2-5H5" fill="none" stroke="#fff" stroke-width="1.5"/><circle cx="6" cy="11" r="1.3" fill="#fff"/><circle cx="12" cy="11" r="1.3" fill="#fff"/></svg></div></div>
<div class="abs card" style="left:407px;top:638px"><div class="img" role="img" aria-label="Grey printed t-shirt" style="background:radial-gradient(#6e7470 45%,#f6f6f6 65%)"></div><div class="name">CREATIVE SHIRT</div><div class="price">$24</div><div class="corner"><svg width="16" height="13" viewBox="0 0 16 13"><path d="M0 1h3l2 7h8l2-5H5" fill="none" stroke="#fff" stroke-width="1.5"/><circle cx="6" cy="11" r="1.3" fill="#fff"/><circle cx="12" cy="11" r="1.3" fill="#fff"/></svg></div></div>
<div class="abs card" style="left:544px;top:638px"><div class="img" role="img" aria-label="Black walking shoes" style="background:radial-gradient(ellipse 55% 35%,#2a2a2a 55%,#f6f6f6 75%)"></div><div class="stars">★★★★<i>★</i></div><div class="name">WALKING SHOES</div><div class="price"><s>$22</s>$19</div><div class="corner"><svg width="16" height="13" viewBox="0 0 16 13"><path d="M0 1h3l2 7h8l2-5H5" fill="none" stroke="#fff" stroke-width="1.5"/><circle cx="6" cy="11" r="1.3" fill="#fff"/><circle cx="12" cy="11" r="1.3" fill="#fff"/></svg></div></div>
<div class="abs sect" style="top:825px">ITEMS FROM SELLER STORES</div>
<div class="abs sl l" style="left:114px;top:938px"></div><div class="abs sl r" style="left:672px;top:938px"></div>
<div class="abs card" style="left:137px;top:854px"><div class="img" role="img" aria-label="Navy and red holdall bag" style="background:radial-gradient(#2b3a63 30%,#b8343a 45%,#f5f5f5 62%)"></div><div class="name">BAG</div><div class="price"><s>$22</s>$19</div><div class="corner"><svg width="16" height="13" viewBox="0 0 16 13"><path d="M0 1h3l2 7h8l2-5H5" fill="none" stroke="#fff" stroke-width="1.5"/><circle cx="6" cy="11" r="1.3" fill="#fff"/><circle cx="12" cy="11" r="1.3" fill="#fff"/></svg></div></div>
<div class="abs card" style="left:269px;top:854px"><div class="img" role="img" aria-label="Brown tinted aviator sunglasses" style="background:radial-gradient(ellipse 55% 25%,#b89272 55%,#f6f6f6 75%)"></div><div class="stars">★★★★<i>★</i></div><div class="name">WOMAN GLASSES</div><div class="price">$39</div><div class="corner"><svg width="16" height="13" viewBox="0 0 16 13"><path d="M0 1h3l2 7h8l2-5H5" fill="none" stroke="#fff" stroke-width="1.5"/><circle cx="6" cy="11" r="1.3" fill="#fff"/><circle cx="12" cy="11" r="1.3" fill="#fff"/></svg></div></div>
<div class="abs card" style="left:407px;top:854px"><div class="img" role="img" aria-label="Rust orange printed t-shirt" style="background:radial-gradient(#b8471c 45%,#f6f6f6 65%)"></div><div class="name">CREATIVE SHIRT</div><div class="price">$24</div><div class="corner"><svg width="16" height="13" viewBox="0 0 16 13"><path d="M0 1h3l2 7h8l2-5H5" fill="none" stroke="#fff" stroke-width="1.5"/><circle cx="6" cy="11" r="1.3" fill="#fff"/><circle cx="12" cy="11" r="1.3" fill="#fff"/></svg></div></div>
<div class="abs card" style="left:544px;top:854px"><div class="img" role="img" aria-label="Grey canvas high-top sneakers" style="background:radial-gradient(ellipse 55% 40%,#5c5c5c 50%,#f6f6f6 75%)"></div><div class="stars">★★★★<i>★</i></div><div class="name">WALKING SHOES</div><div class="price"><s>$22</s>$19</div><div class="corner"><svg width="16" height="13" viewBox="0 0 16 13"><path d="M0 1h3l2 7h8l2-5H5" fill="none" stroke="#fff" stroke-width="1.5"/><circle cx="6" cy="11" r="1.3" fill="#fff"/><circle cx="12" cy="11" r="1.3" fill="#fff"/></svg></div></div>
<div class="abs footer">
<div class="col" style="left:120px"><h5>Information</h5><div>Advertising</div><div>Knowledge Base</div><div>Forum</div><div>Stores</div><div>Want Ads</div></div>
<div class="col" style="left:246px"><h5>Buy</h5><div>Categories</div><div>Search</div><div>Currency Converter</div></div>
<div class="col" style="left:360px"><h5>Sell</h5><div>Sell New Item</div><div>Sell Bulk Items</div><div>Nonprofits</div></div>
<div class="col" style="left:474px"><h5>Support</h5><div>Contact</div><div>Terms</div><div>Privacy</div><div>RSS</div></div>
<div class="col" style="left:577px"><h5>Other</h5><div>Find work or talent</div><div>Post a job</div><div>About</div><div>News</div><div>Feeds</div></div></div>
<div class="abs bottom"><span class="abs" style="left:120px;top:17px">Copyright ©2014, bidwell.co.uk.</span>
<div class="abs soc" style="left:547px;background:#2f5fa8"></div><div class="abs soc" style="left:581px;background:#3fa9df"></div>
<div class="abs soc" style="left:615px;background:#1c1c1c"><svg class="abs" style="left:8px;top:8px" width="11" height="11"><path d="M5.5 0v11M0 5.5h11" stroke="#fff" stroke-width="1.6"/></svg></div>
<div class="abs soc" style="left:649px;background:#d02a2a"></div></div>
</body></html>
```